Launch Website

A very simple, but attractive website (template preferred) is required in a common format - HTML5 or Wordpress etc.
It should be easily user updateable for updates.
Pages it needs:
-Home Page with menu bar, company logo and 1 large graphic/picture and two smaller graphics/logos.
- What we do
- How we do it
- About Us
- Guarantees
- Results
- Contact Page with Enquiry Form
- Provision for a blog to be added later

Most pages will be approx 150 words text with some small/medium images.
We have our own domain & hosting.

A "less is more" design approach would be encouraged.

Target Market(s)

Vehicle Fleet Managers

Industry/Entity Type

It Company

Font styles to use
Sans Serif

Colors
9bcb3c

Requirements
Must have
• Corporate Style. No Fluff.
Nice to have
• Images of LIght Commerical vehicles and trucks

Am ok with white background throughout site.
Colours should match/complement company logo.
Should not have
• Should not be too "busy"

```html
<!DOCTYPE html>
<html lang="en">
<head>
<meta charset="utf-8">
<title>Northway Fleet – Home</title>
<link rel="stylesheet" href="https://fonts.googleapis.com/css2?family=Questrial&family=PT+Sans:wght@400;700&family=PT+Sans+Narrow:wght@400;700&display=swap">
<style>
  :root {
    --brand-green: #009e47;
    --nav-dark: #1d2029;
    --text-grey: #5a5a5a;
    --white: #ffffff;
    --badge-dark: #2a2a2c;
    --badge-grey: #c9c9c9;
  }
  * { box-sizing: border-box; margin: 0; padding: 0; }
  html, body { width: 1099px; height: 1200px; overflow: hidden; background: var(--white); }
  body { position: relative; font-family: "PT Sans", sans-serif; }

  .site-header { position: absolute; left: 0; top: 0; width: 1099px; height: 109px; }
  .brand-name {
    position: absolute; left: 28px; top: 12px;
    font-family: "Questrial", sans-serif; font-size: 68px; line-height: 1;
    color: var(--brand-green); letter-spacing: 1px; white-space: nowrap;
  }
  .partner-badge { position: absolute; }
  .partner-badge--pill { left: 765px; top: 57px; width: 163px; height: 37px; border-radius: 9px; background: var(--badge-dark); }
  .partner-badge--block { left: 953px; top: 34px; width: 112px; height: 56px; border-radius: 4px; background: var(--badge-grey); }

  .hero-band { position: absolute; left: 0; top: 109px; width: 1075px; height: 351px; background: var(--nav-dark); }

  .main-nav {
    position: absolute; left: 21px; top: 109px; width: 1054px; height: 48px;
    display: flex; align-items: stretch; background: var(--nav-dark);
  }
  .main-nav a {
    display: flex; align-items: center; justify-content: center;
    color: var(--white); text-decoration: none; text-transform: uppercase;
    font-size: 17px; flex: 1 1 auto; white-space: nowrap;
  }
  .main-nav a.is-active { background: var(--brand-green); flex: 0 0 116px; }

  .hero-frame { position: absolute; left: 21px; top: 157px; width: 1054px; height: 436px; background: var(--white); }
  .hero-photo {
    position: absolute; left: 29px; top: 165px; width: 1039px; height: 419px;
    background: linear-gradient(180deg, #2c3a58 0%, #5d7397 30%, #9ba9bd 48%, #d9dbe0 62%, #b9bcc3 78%, #1b1c22 100%);
  }

  .process-steps { position: absolute; left: 0; top: 660px; width: 1099px; }
  .step { position: absolute; width: 390px; }
  .step-icon { position: absolute; left: -93px; top: 0; width: 73px; height: 73px; }
  .step-title { font-family: "PT Sans Narrow", sans-serif; font-weight: 700; font-size: 19.5px; color: var(--text-grey); line-height: 1.1; }
  .step-text { font-family: "PT Sans Narrow", sans-serif; font-size: 14.5px; line-height: 19px; color: var(--text-grey); margin-top: 3px; }
  .step--trial { left: 155px; top: 0; }
  .step--assess { left: 696px; top: 0; }
  .step--rollout { left: 155px; top: 124px; }
  .step--monitor { left: 696px; top: 124px; }

  .site-footer { position: absolute; left: 0; top: 951px; width: 1099px; height: 249px; background: var(--brand-green); color: var(--white); text-align: center; }
  .social-links { position: absolute; top: 61px; left: 0; width: 100%; display: flex; justify-content: center; gap: 16px; }
  .social-links span { width: 48px; height: 48px; border-radius: 50%; background: var(--white); display: block; }
  .footer-nav { position: absolute; top: 161px; width: 100%; font-family: Arial, Helvetica, sans-serif; font-size: 13.5px; }
  .footer-nav a { color: var(--white); text-decoration: none; }
  .copyright { position: absolute; top: 183px; width: 100%; font-family: Arial, Helvetica, sans-serif; font-size: 12px; }
</style>
</head>
<body>
  <header class="site-header">
    <div class="brand-name">Northway Fleet</div>
    <div class="partner-badge partner-badge--pill" aria-hidden="true"></div>
    <div class="partner-badge partner-badge--block" aria-hidden="true"></div>
  </header>

  <div class="hero-band"></div>
  <nav class="main-nav">
    <a class="is-active" href="#">Home</a>
    <a href="#">What we do</a>
    <a href="#">How we do it</a>
    <a href="#">About us</a>
    <a href="#">Guarantees</a>
    <a href="#">Results</a>
    <a href="#">Contact us</a>
  </nav>
  <div class="hero-frame"></div>
  <div class="hero-photo" role="img" aria-label="Photo of an orange truck between two rows of white trucks under a cloudy blue sky"></div>

  <section class="process-steps">
    <div class="step step--trial">
      <svg class="step-icon" viewBox="0 0 73 73" aria-hidden="true" fill="#009e47">
        <rect x="0" y="12" width="17" height="40"/><rect x="27" y="31" width="17" height="21"/><rect x="54" y="0" width="19" height="52"/><rect x="0" y="56" width="73" height="5"/>
      </svg>
      <h2 class="step-title">Progress to Trial</h2>
      <p class="step-text">Lorem ipsum dolor sit amet, consectetuer adipiscing elit, sed diam nonummy nibh euismod tincidunt ut laoreet dolore magna aliquam erat volutpat. Ut wisi enim ad minim veniam, quis nostrud.</p>
    </div>
    <div class="step step--assess">
      <svg class="step-icon" viewBox="0 0 73 73" aria-hidden="true">
        <path d="M40 8 H12 Q5 8 5 15 V59 Q5 66 12 66 H56 Q63 66 63 59 V36" fill="none" stroke="#009e47" stroke-width="8"/>
        <path d="M60 2 L71 13 L40 44 L27 47 L30 34 Z" fill="#009e47"/>
      </svg>
      <h2 class="step-title">Assess Trial Results</h2>
      <p class="step-text">Adipiscing elit, sed diam nonummy nibh euismod tincidunt ut laoreet dolore magna aliquam erat volutpat. Ut wisi enim ad minim veniam, quis nostrud exerci tation ullamcorper .</p>
    </div>
    <div class="step step--rollout">
      <svg class="step-icon" viewBox="0 0 73 73" aria-hidden="true" fill="#009e47">
        <path d="M0 8 H44 V20 H58 L72 36 V56 H0 Z"/>
        <circle cx="14" cy="58" r="7" fill="#fff"/><circle cx="14" cy="58" r="5"/>
        <circle cx="58" cy="58" r="7" fill="#fff"/><circle cx="58" cy="58" r="5"/>
        <path d="M48 24 H56 L65 35 H48 Z" fill="#fff"/>
      </svg>
      <h2 class="step-title">Rollout to balance of Fleet</h2>
      <p class="step-text">Diam nonummy nibh euismod tincidunt ut laoreet dolore magna aliquam erat volutpat. Ut wisi enim ad minim veniam, quis nostrud exerci tation ullamcorper suscipit lobortis nisl ut aliquip ex.</p>
    </div>
    <div class="step step--monitor">
      <svg class="step-icon" viewBox="0 0 73 73" aria-hidden="true">
        <rect x="0" y="0" width="70" height="70" fill="#009e47"/>
        <rect x="7" y="16" width="56" height="47" fill="#fff"/>
        <rect x="7" y="6" width="4" height="4" fill="#fff"/><rect x="14" y="6" width="4" height="4" fill="#fff"/><rect x="21" y="6" width="4" height="4" fill="#fff"/>
        <polyline points="11,46 20,36 28,46 37,32 46,46 52,40 60,40" fill="none" stroke="#009e47" stroke-width="4"/>
      </svg>
      <h2 class="step-title">Monitor ongoing cost savings</h2>
      <p class="step-text">Lorem ipsum dolor sit amet, consectetuer adipiscing elit, sed diam nonummy nibh euismod tincidunt ut laoreet dolore magna aliquam erat volutpat. Ut wisi enim ad minim veniam,.</p>
    </div>
  </section>

  <footer class="site-footer">
    <div class="social-links" aria-hidden="true"><span></span><span></span><span></span><span></span><span></span></div>
    <nav class="footer-nav">
      <a href="#">Home</a> · <a href="#">About Us</a> · <a href="#">Products</a> · <a href="#">Features</a> · <a href="#">Options</a> · <a href="#">Replacement Parts</a> · <a href="#">FAQ's</a> · <a href="#">Library</a> · <a href="#">Videos</a> · <a href="#">Contact Us</a>
    </nav>
    <p class="copyright">© Copyright 2002 - 2013 Company Name. All Rights Reserved</p>
  </footer>
</body>
</html>
```